Accountability Project Graphics

I want to create 10 social media graphics (new Instagram size 4:5 (1080 x 1350 pixels) focusing on our Quilvo Accountability App, using any of the 3 pictures attached. Use the attached pics only, NO RANDOM STOCK PHOTOGRAPHY. For the color scheme, use the landing page colors/fonts (attached).
You can add any of the 3 photos attached but I mainly need BOLD text that includes these headlines and sub-headlines on them.
Please NOTE for all the headlines below, also add this sub-headline on each graphic:
Stay Consistent with RT in Your Pocket!
Here are the headlines:
• Stop Starting Over Every Monday
• You don't need more willpower. You need more support
• Built for women who are tired of doing this alone
• When Motivation Fades, RT Checks In
• The Support System You've Been Missing
• Support When Motivation Disappears
• What if RT Checked in Every Day?
• The Missing Piece Isn't Another Diet
• Eat the food you love. Stay accountable every day.
• One Bad Meal Doesn't Mean You Failed
women over 40 trying to lose weight

```html
<!DOCTYPE html>
<html lang="en">
<head>
<meta charset="utf-8">
<title>Quilvo Accountability – Social Graphics</title>
<link href="https://fonts.googleapis.com/css2?family=Playfair+Display:wght@800;900&family=Plus+Jakarta+Sans:wght@400;500;600&display=swap" rel="stylesheet">
<style>
  :root{
    --stage:#1d0a15;
    --pink:#e0457b;
    --pink-deep:#d23a70;
    --plum:#2a0f2c;
    --blush:#fdeef3;
    --blush-2:#f9d3e1;
    --rose:#f2a3c0;
    --white:#ffffff;
    --serif:"Playfair Display", Georgia, serif;
    --sans:"Plus Jakarta Sans", Arial, sans-serif;
  }
  *{box-sizing:border-box;margin:0;padding:0}
  html,body{width:1200px;height:945px;overflow:hidden;background:var(--stage)}
  .canvas{position:relative;width:1200px;height:945px}
  .post{position:absolute;overflow:hidden;background:linear-gradient(180deg,var(--blush) 0%,var(--blush-2) 100%);color:var(--plum)}
  .post--grid{width:222px;height:277px}
  .photo{position:absolute}
  .photo--fade{background:linear-gradient(180deg,rgba(201,136,159,.75) 0%,rgba(233,180,199,.45) 55%,rgba(249,211,225,0) 100%)}
  .sans{font-family:var(--sans);font-weight:500;color:var(--pink);letter-spacing:-.04em;line-height:1}
  .serif{font-family:var(--serif);font-weight:900;color:var(--plum);letter-spacing:-.02em;line-height:1}
  .tagline{font-family:var(--sans);font-weight:500;font-size:7.5px;letter-spacing:-.03em;color:var(--plum);white-space:nowrap}
  .tagline--pink{color:var(--pink)}
  .pill{display:inline-block;border:1px solid var(--pink);border-radius:30px;background:var(--white);padding:2px 9px}
  .center{position:absolute;left:0;right:0;text-align:center}
  .bar{border-left:1.5px solid var(--plum);padding-left:10px}

  .feature{left:60px;top:247px;width:360px;height:450px}
  .feature .photo{left:0;top:70px;width:190px;height:320px;border-radius:0 30px 30px 0;
    background:linear-gradient(170deg,#d98ba8 0%,#3a2230 55%,#f3bfd2 100%)}
  .feature .copy{position:absolute;left:208px;top:104px;width:140px}
  .feature .sans{font-size:29px;line-height:1.1}
  .feature .serif{font-size:42px;margin-top:8px;line-height:1.05}
  .feature .rule{height:1px;background:var(--pink);margin:12px 0 10px}
  .feature .tagline{font-size:12.5px;white-space:normal;line-height:1.3}
</style>
</head>
<body>
<main class="canvas">

  <section class="post feature">
    <div class="photo" role="img" aria-label="Smiling coach in a black lace top, hand on hip, framed like a phone screen"></div>
    <div class="copy">
      <p class="sans">One Bad Meal Doesn't Mean</p>
      <p class="serif">You Failed.</p>
      <div class="rule"></div>
      <p class="tagline">Stay Consistent with RT in Your Pocket!</p>
    </div>
  </section>

  <!-- Row 1 -->
  <section class="post post--grid" style="left:475px;top:50px">
    <div class="photo photo--fade" role="img" aria-label="Two women hugging and laughing" style="left:0;top:0;width:222px;height:170px"></div>
    <div class="center" style="top:66px">
      <span class="pill sans" style="font-size:12px">You Don't</span>
      <p class="sans" style="font-size:25px;margin-top:2px">Need More</p>
      <p class="serif" style="font-size:27px">Willpower.</p>
      <span class="pill sans" style="font-size:15px;padding:3px 16px;margin-top:4px">You Need More.</span>
      <p class="serif" style="font-size:29px;margin-top:3px">Support<span style="color:var(--pink)">.</span></p>
      <p class="tagline" style="margin-top:10px">Stay Consistent with RT in Your Pocket!</p>
    </div>
  </section>

  <section class="post post--grid" style="left:702px;top:50px;background:linear-gradient(180deg,#fff4f7,#fbe3ec)">
    <div style="position:absolute;left:25px;top:80px">
      <p class="sans" style="font-size:19px;line-height:1.05">When<br>Motivation<br>Fades,</p>
      <div class="bar" style="margin-top:12px"><p class="serif" style="font-size:23px">RT<br>Checks In</p></div>
      <p class="tagline tagline--pink" style="margin-top:12px">Stay Consistent with RT in Your Pocket!</p>
    </div>
  </section>

  <section class="post post--grid" style="left:929px;top:50px">
    <div class="photo photo--fade" role="img" aria-label="Two women embracing in a store" style="left:0;top:0;width:222px;height:200px"></div>
    <div class="center" style="top:143px">
      <p class="sans" style="font-size:26px">The<br>Missing Piece</p>
      <span class="pill sans" style="font-size:14px;color:var(--plum);border-color:var(--plum);padding:1px 9px">Isn't</span>
      <p class="serif" style="font-size:27px">Another Diet.</p>
      <p class="tagline" style="margin-top:8px">Stay Consistent with RT in Your Pocket!</p>
    </div>
  </section>

  <!-- Row 2 -->
  <section class="post post--grid" style="left:475px;top:332px;background:#fdf0f4">
    <svg width="222" height="277" style="position:absolute;left:0;top:0" aria-hidden="true">
      <path d="M-10 40 C40 0 90 20 95 70" fill="none" stroke="var(--rose)" stroke-width="22" opacity=".6"/>
      <path d="M20 200 C40 270 150 270 190 200" fill="none" stroke="var(--rose)" stroke-width="22" opacity=".6"/>
    </svg>
    <div class="photo" role="img" aria-label="Smiling coach in a black lace top, hand on hip" style="left:0;top:40px;width:115px;height:237px;background:linear-gradient(170deg,#c98aa2,#3a2230 60%,#2a1a24)"></div>
    <div style="position:absolute;left:122px;top:94px;width:92px">
      <p class="serif" style="font-size:21px">Built for<br>Women</p>
      <p class="sans" style="font-size:12.5px;line-height:1.05;margin-top:3px">who are tired of doing this alone.</p>
      <p class="tagline" style="white-space:normal;margin-top:8px;line-height:1.3">Stay Consistent with RT in Your Pocket!</p>
    </div>
  </section>

  <section class="post post--grid" style="left:702px;top:332px;background:#fdf0f4">
    <svg width="222" height="277" style="position:absolute;left:0;top:0" aria-hidden="true">
      <path d="M130 0 C125 40 170 80 222 50" fill="none" stroke="var(--pink-deep)" stroke-width="10"/>
      <circle cx="20" cy="180" r="45" fill="none" stroke="var(--rose)" stroke-width="12"/>
    </svg>
    <div style="position:absolute;left:35px;top:30px;width:151px;height:93px;background:var(--blush-2);border-radius:4px"></div>
    <div class="center" style="top:42px">
      <p class="sans" style="font-size:12px">Stop Starting</p>
      <span class="pill sans" style="font-size:7px;padding:1px 7px">Over</span>
      <p class="serif" style="font-size:25px">Every<br>Monday</p>
    </div>
    <div class="photo" role="img" aria-label="Two women in denim shirts laughing together" style="left:35px;top:125px;width:160px;height:152px;background:linear-gradient(180deg,#9a6b7c,#4a5f86)"></div>
    <div class="center" style="top:238px"><span class="pill tagline tagline--pink">Stay Consistent with RT in Your Pocket!</span></div>
  </section>

  <section class="post post--grid" style="left:929px;top:332px;background:#fdf0f4">
    <div class="photo" role="img" aria-label="Two women laughing together" style="left:20px;top:150px;width:202px;height:127px;background:linear-gradient(0deg,rgba(201,136,159,.6),rgba(233,180,199,.2))"></div>
    <div style="position:absolute;left:25px;top:27px">
      <p class="sans" style="font-size:19px">Eat The Food</p>
      <p class="serif" style="font-size:24px">You Love.</p>
      <div class="bar" style="margin-top:10px">
        <p class="sans" style="font-size:19px">Stay Accountable</p>
        <p class="serif" style="font-size:24px">Every Day.</p>
      </div>
      <span class="pill tagline tagline--pink" style="margin-top:9px">Stay Consistent with RT in Your Pocket!</span>
    </div>
  </section>

  <!-- Row 3 -->
  <section class="post post--grid" style="left:475px;top:614px">
    <div class="center" style="top:72px">
      <p class="serif" style="font-size:32px">Supp<span role="img" aria-label="Two women in denim inside a circle" style="display:inline-block;width:40px;height:40px;border-radius:50%;vertical-align:-6px;background:linear-gradient(180deg,#9a6b7c,#4a5f86);border:3px solid var(--pink-deep)"></span>rt</p>
    </div>
    <div style="position:absolute;left:35px;top:120px">
      <p class="sans" style="font-size:21px;padding-left:22px">When</p>
      <p class="serif" style="font-size:22px;color:var(--pink);padding-left:33px">Motivation</p>
      <p class="sans" style="font-size:21px">Disappears.</p>
    </div>
    <p class="tagline center" style="top:200px">Stay Consistent with RT in Your Pocket!</p>
  </section>

  <section class="post post--grid" style="left:702px;top:614px">
    <div class="photo" role="img" aria-label="Two women standing together, faded" style="left:0;top:60px;width:222px;height:217px;background:linear-gradient(180deg,rgba(233,180,199,0),rgba(201,136,159,.35) 50%,rgba(233,180,199,.2))"></div>
    <p class="serif" style="position:absolute;left:20px;top:28px;font-size:22px;color:var(--pink)">The Support<br>System,</p>
    <p class="tagline tagline--pink center" style="top:133px">Stay Consistent with RT in Your Pocket!</p>
    <p class="serif" style="position:absolute;right:20px;top:206px;font-size:22px;text-align:right">You've Been<br>Missing.</p>
  </section>

  <section class="post post--grid" style="left:929px;top:614px;background:linear-gradient(180deg,#fff6f9,#fbe3ec)">
    <div style="position:absolute;left:56px;top:62px;transform:rotate(-2deg);background:var(--plum);padding:6px 12px">
      <p class="sans" style="font-size:26px;color:var(--white)">What If</p>
    </div>
    <div style="position:absolute;left:19px;top:106px;transform:rotate(-3deg);background:var(--pink-deep);padding:6px 10px">
      <p class="sans" style="font-size:26px;color:var(--white)">RT Checked In</p>
    </div>
    <div style="position:absolute;left:28px;top:157px;transform:rotate(2deg);background:var(--white);border:1px solid #d9c5cf;padding:4px 16px">
      <p class="sans" style="font-size:26px;color:var(--plum)">Every Day?</p>
    </div>
    <p class="tagline center" style="top:213px">Stay Consistent with RT in Your Pocket!</p>
  </section>

</main>
</body>
</html>
```